Membership Based Medical Practice Website

We need a functioning website for a new Membership based medical practice. There will be an enrollment fee and a monthly fee. We would like to see designs that are modern, simple. Should use neutral light colors. Examples of sites we like are www.kellanmoorclinic.com and https://fernholtcare.com/ We also have a link that when "Join Now" is clicked it will go to the signup website.

Target Market(s)

Gay Men, local population, Age group 20 to 60's.

Industry/Entity Type

Medical

Coding

Coded - Design and coding required

Number of Pages Required

5+ page

Font styles to use
Sans Serif

Colors
ffffff
cee9f5
ecf7fb
cfeae6
edf8f6
aaaaaa
e9e9e9
dbdbdb
fff3d1

Requirements
Must have
• Logo and header on every page. Clean, simple design, clear content, mobile compatible.
• Must use Wordpress
Nice to have
• Ideas should come from kellanmoorclinic.com
• Easy to read
Should not have
• Generic patient pictures, bold colors.
• Should not copy from above websites.

```html
<!DOCTYPE html>
<html lang="en">
<head>
<meta charset="utf-8">
<title>Larkspur Infectious Disease Specialists</title>
<link rel="stylesheet" href="https://fonts.googleapis.com/css2?family=Roboto:wght@300;400;500;700;900&display=swap">
<style>
:root{
  --white:#ffffff;
  --ink:#1d1d1d;
  --text:#333333;
  --muted:#5a5a5a;
  --mint:#cfeae6;
  --gold:#c9a55a;
  --rule:#dbdbdb;
  --card:#6b6b6d;
  --band:#e9e9e9;
  --footer:#232323;
  --footer-text:#e8e8e8;
}
*{margin:0;padding:0;box-sizing:border-box}
html,body{width:1200px;height:3000px;overflow:hidden;background:var(--white)}
body{font-family:'Roboto',sans-serif;color:var(--text);position:relative}
.abs{position:absolute}
svg{display:block}

/* header */
.hero-photo{left:0;top:100px;width:1200px;height:590px;
  background:linear-gradient(180deg,#c9cccd 0%,#b9bdbd 35%,#8f968c 55%,#5d6a4c 72%,#3b3f3a 100%)}
.header-shapes{left:0;top:0}
.brand{left:110px;top:58px;width:300px;text-align:center;color:#6a6a6a;font-weight:400}
.brand-mark{width:58px;height:58px;border:2px solid var(--gold);border-radius:50%;margin:0 auto 14px}
.brand-name{font-size:20px;letter-spacing:14px;padding-left:14px}
.brand-sub{font-size:15px;letter-spacing:.5px;margin-top:4px}
.phone{left:892px;top:10px;display:flex;align-items:center;gap:14px;font-size:19px;color:var(--ink)}
.phone-icon{width:40px;height:40px;border-radius:50%;background:var(--mint);display:flex;align-items:center;justify-content:center}
.nav{left:576px;top:64px;display:flex;gap:22px;font-size:14px;color:var(--ink);align-items:center}

.hero-title{left:0;width:1200px;top:306px;text-align:center;font-size:56px;font-weight:700;color:#1a1a1a;text-shadow:0 4px 10px rgba(0,0,0,.35)}
.hero-sub{left:0;width:1200px;top:392px;text-align:center;font-size:23px;color:#1a1a1a}
.btn{background:var(--mint);color:var(--ink);font-size:17px;font-weight:500;display:flex;align-items:center;justify-content:center}
.hero-btn{left:520px;top:460px;width:170px;height:52px}
.dots{left:1124px;top:358px}

/* specialties */
.intro-title{left:0;width:1200px;top:772px;text-align:center;font-size:26px;font-weight:500;color:var(--ink)}
.intro-sub{left:0;width:1200px;top:826px;text-align:center;font-size:21px;color:var(--ink)}
.grid-rule{left:146px;top:1078px;width:898px;height:2px;background:var(--rule)}
.cell-rule{width:2px;background:#bdbdbd}
.spec{width:206px;text-align:center;font-size:19px;color:var(--ink);line-height:1.55}
.spec svg{margin:0 auto 12px}

/* band */
.band{left:0;top:1326px;width:1200px;height:258px;background:linear-gradient(90deg,#1e1e1e,#4a4442 45%,#3a3a3a 60%,#1d1d1d)}
.band-text{left:0;top:1402px;width:1200px;text-align:center;color:var(--white);font-size:31px;line-height:48px;font-weight:400}

/* features */
.feature{background:var(--card);color:var(--white);text-align:center;padding:36px 10px 0}
.feature svg{margin:0 auto 18px}
.feature h3{font-size:17px;font-weight:700;margin-bottom:12px}
.feature p{font-size:13px;line-height:24px;font-weight:500}
.feature.active{background:var(--white);color:var(--ink);border:3px solid #111;padding-top:36px}
.feature.active h3{font-size:18px;font-weight:500}
.feature.active p{color:#777;font-size:14px;font-weight:400}
.arrow{width:48px;height:48px;border-radius:50%;background:#111;display:flex;align-items:center;justify-content:center}

/* pricing */
.pricing{left:0;top:2060px;width:1200px;height:560px;background:var(--band)}
.pricing-title{left:110px;top:2140px;font-size:44px;font-weight:700;color:var(--ink)}
.pricing-lead{left:112px;top:2214px;width:520px;font-size:21px;line-height:32px;color:#5c5c5c}
.perks{left:112px;top:2330px;list-style:none;font-size:14px;color:#444}
.perks li{display:flex;align-items:center;gap:16px;height:30px}
.pricing-btn{left:112px;top:2508px;width:170px;height:50px}
.photo-shadow{left:682px;top:2166px;width:422px;height:322px;background:#000;border-radius:10px}
.pricing-photo{left:664px;top:2150px;width:424px;height:322px;border-radius:12px;
  background:linear-gradient(180deg,#e8dccd 0%,#f3d3a6 40%,#d8a874 62%,#6e5648 85%,#3b2f2b 100%)}

/* footer */
.footer{left:0;top:2600px}
.foot-brand{left:126px;top:2680px;width:300px;text-align:center;color:var(--footer-text);font-weight:400}
.foot-brand .brand-mark{border-color:var(--footer-text)}
.socials{left:204px;top:2872px;display:flex;gap:12px}
.socials span{width:26px;height:26px;border:2px solid var(--footer-text);border-radius:50%}
.foot-h{font-size:20px;font-weight:700;color:var(--white)}
.foot-links{list-style:none;font-size:14px;color:var(--footer-text);font-weight:500}
.foot-links li{height:29px;display:flex;align-items:center;gap:14px}
.foot-links li::before{content:"";border-left:6px solid #9a9a9a;border-top:4px solid transparent;border-bottom:4px solid transparent}
.contact{font-size:14px;color:var(--footer-text);font-weight:500;line-height:26px}
.contact .row{display:flex;gap:18px;align-items:flex-start;margin-bottom:14px}
.foot-rule{left:110px;top:2930px;width:980px;height:1px;background:#444}
.legal{top:2956px;font-size:12px;color:var(--footer-text);font-weight:500}
</style>
</head>
<body>

<!-- header & hero -->
<div class="abs hero-photo" role="img" aria-label="Misty highland road stretching toward distant hills with grazing sheep"></div>
<svg class="abs header-shapes" width="1200" height="700" viewBox="0 0 1200 700">
  <rect x="0" y="0" width="1200" height="100" fill="#fff"/>
  <path d="M0 0 H490 C470 150 380 206 240 206 C120 206 40 182 0 150 Z" fill="#fff"/>
  <path d="M0 680 H490 C545 680 555 650 600 650 C645 650 655 680 710 680 H1200 V700 H0 Z" fill="#fff"/>
  <circle cx="600" cy="672" r="9" fill="none" stroke="#222" stroke-width="1.6"/>
  <path d="M596 670 L600 674 L604 670" fill="none" stroke="#222" stroke-width="1.6"/>
</svg>
<div class="abs brand">
  <div class="brand-mark"></div>
  <div class="brand-name">LARKSPUR</div>
  <div class="brand-sub">INFECTIOUS DISEASE SPECIALISTS</div>
</div>
<div class="abs phone">
  <span class="phone-icon"><svg width="20" height="20" viewBox="0 0 24 24"><path d="M6.6 10.8a15.1 15.1 0 0 0 6.6 6.6l2.2-2.2a1 1 0 0 1 1-.25 11.4 11.4 0 0 0 3.6.57 1 1 0 0 1 1 1V20a1 1 0 0 1-1 1A17 17 0 0 1 3 4a1 1 0 0 1 1-1h3.5a1 1 0 0 1 1 1c0 1.25.2 2.45.57 3.57a1 1 0 0 1-.25 1Z" fill="none" stroke="#333" stroke-width="1.5"/></svg></span>
  (555) 204 7781
</div>
<nav class="abs nav">
  <span>Home</span><span>Specialties</span><span>Pricing</span><span>About Us</span><span>Faq</span><span>Blog</span><span>Join Us</span>
  <svg width="14" height="14" viewBox="0 0 14 14"><circle cx="6" cy="6" r="4.5" fill="none" stroke="#111" stroke-width="2"/><path d="M9.5 9.5 L13 13" stroke="#111" stroke-width="2"/></svg>
</nav>

<h1 class="abs hero-title">Larkspur Infectious Disease</h1>
<p class="abs hero-sub">Specialty medicine with Commitment, Compassion and Care</p>
<div class="abs btn hero-btn">Read More</div>
<svg class="abs dots" width="32" height="90" viewBox="0 0 32 90">
  <circle cx="16" cy="16" r="13" fill="none" stroke="#fff" stroke-width="2"/>
  <circle cx="16" cy="16" r="8" fill="#fff"/>
  <circle cx="16" cy="50" r="7" fill="#fff"/>
  <circle cx="16" cy="78" r="7" fill="#fff"/>
</svg>

<!-- specialties -->
<h2 class="abs intro-title">We offer comprehensive treatment of a wide variety of infectious diseases.</h2>
<p class="abs intro-sub">Our expertise is in the following area.</p>

<div class="abs cell-rule" style="left:393px;top:922px;height:134px"></div>
<div class="abs cell-rule" style="left:601px;top:922px;height:134px"></div>
<div class="abs cell-rule" style="left:803px;top:922px;height:134px"></div>
<div class="abs grid-rule"></div>
<div class="abs cell-rule" style="left:393px;top:1104px;height:134px"></div>
<div class="abs cell-rule" style="left:601px;top:1104px;height:134px"></div>
<div class="abs cell-rule" style="left:803px;top:1104px;height:134px"></div>

<div class="abs spec" style="left:158px;top:936px">
  <svg width="48" height="54" viewBox="0 0 48 54" fill="none" stroke="#111" stroke-width="2"><ellipse cx="24" cy="26" rx="10" ry="16" transform="rotate(30 24 26)"/><circle cx="24" cy="26" r="3"/><path d="M10 46 L16 40 M38 6 L32 12"/></svg>
  HIV/PrEP
</div>
<div class="abs spec" style="left:394px;top:936px">
  <svg width="52" height="54" viewBox="0 0 52 54" fill="none" stroke="#111" stroke-width="2"><path d="M8 22 C8 10 44 8 44 22 C44 38 20 46 12 40 C6 35 8 28 8 22 Z"/><path d="M20 24 L32 20"/></svg>
  Chronic Hepatitis
</div>
<div class="abs spec" style="left:600px;top:928px">
  <svg width="52" height="56" viewBox="0 0 52 56" fill="none" stroke="#111" stroke-width="2"><circle cx="22" cy="24" r="12"/><path d="M22 36 V52 M15 45 H29 M31 15 L44 3 M36 3 H44 V11"/></svg>
  Sexually transmitted infections
</div>
<div class="abs spec" style="left:820px;top:928px">
  <svg width="40" height="56" viewBox="0 0 40 56" fill="none" stroke="#111" stroke-width="2"><rect x="13" y="10" width="14" height="30" rx="2"/><path d="M20 2 V10 M12 2 H28 M20 40 V54 M13 20 H20 M13 28 H20"/></svg>
  Pre-travel vaccinations and counselling
</div>

<div class="abs spec" style="left:158px;top:1120px">
  <svg width="54" height="54" viewBox="0 0 54 54" fill="none" stroke="#111" stroke-width="2"><circle cx="27" cy="27" r="12"/><circle cx="27" cy="27" r="4"/><path d="M27 5 V15 M27 39 V49 M5 27 H15 M39 27 H49 M12 12 L19 19 M35 35 L42 42 M42 12 L35 19 M19 35 L12 42"/></svg>
  Postsurgical Infections
</div>
<div class="abs spec" style="left:394px;top:1120px">
  <svg width="54" height="54" viewBox="0 0 54 54" fill="none" stroke="#111" stroke-width="2"><path d="M27 8 V26 M27 22 L20 28 M27 22 L34 28"/><path d="M20 16 C10 16 6 36 8 42 C10 46 20 44 22 38 Z"/><path d="M34 16 C44 16 48 36 46 42 C44 46 34 44 32 38 Z"/></svg>
  Tuberculosis
</div>
<div class="abs spec" style="left:600px;top:1110px">
  <svg width="48" height="56" viewBox="0 0 48 56" fill="none" stroke="#111" stroke-width="2"><rect x="16" y="4" width="16" height="48" rx="8"/><path d="M16 16 H32 M16 28 H32 M16 40 H32 M6 20 H16 M32 20 H42"/></svg>
  Bone and Joint infections
</div>
<div class="abs spec" style="left:820px;top:1118px">
  <svg width="58" height="58" viewBox="0 0 58 58" fill="none" stroke="#111" stroke-width="2.5"><circle cx="29" cy="29" r="26"/><path d="M29 16 V42 M16 29 H42"/></svg>
  More
</div>

<!-- statement band -->
<div class="abs band" role="img" aria-label="Dimly lit coffee mug on a table"></div>
<p class="abs band-text">Less wait, more personal.<br>We are not your traditional doctor’s office.</p>

<!-- features -->
<div class="abs arrow" style="left:46px;top:1778px"><svg width="14" height="14" viewBox="0 0 14 14"><path d="M9 2 L4 7 L9 12" fill="none" stroke="#fff" stroke-width="2"/></svg></div>
<div class="abs arrow" style="left:1108px;top:1778px"><svg width="14" height="14" viewBox="0 0 14 14"><path d="M5 2 L10 7 L5 12" fill="none" stroke="#fff" stroke-width="2"/></svg></div>

<div class="abs feature" style="left:132px;top:1684px;width:226px;height:258px">
  <svg width="70" height="70" viewBox="0 0 70 70" fill="none" stroke="#fff" stroke-width="2.5"><ellipse cx="26" cy="20" rx="16" ry="5"/><ellipse cx="26" cy="30" rx="16" ry="5"/><ellipse cx="26" cy="40" rx="16" ry="5"/><ellipse cx="26" cy="50" rx="16" ry="5"/><circle cx="48" cy="46" r="14"/><path d="M48 38 V54 M44 42 H51 M45 50 H52"/></svg>
  <h3>Straightforward Pricing</h3>
  <p>We charge all our patients the<br>same low rate - no surprises.</p>
</div>
<div class="abs feature active" style="left:366px;top:1664px;width:230px;height:300px">
  <svg width="70" height="70" viewBox="0 0 70 70" fill="none" stroke="#111" stroke-width="2.5"><rect x="14" y="10" width="38" height="44" rx="3"/><path d="M28 18 H38 M33 13 V23 M20 32 H46 M20 40 H46 M8 46 L16 62 H56 L62 46 Z"/></svg>
  <h3>Available when you are</h3>
  <p>New patient appointments<br>are available within<br>1 week.</p>
</div>
<div class="abs feature" style="left:606px;top:1684px;width:226px;height:258px">
  <svg width="70" height="70" viewBox="0 0 70 70" fill="none" stroke="#fff" stroke-width="2.5"><rect x="30" y="6" width="22" height="14" rx="2"/><path d="M10 44 H60 M16 44 V62 M54 44 V62 M34 30 H56 V44 M40 20 V30"/><rect x="18" y="28" width="12" height="16" rx="3"/></svg>
  <h3>Devoted Care</h3>
  <p>We schedule enough time at<br>each visit to make sure all of<br>your questions are answered.</p>
</div>
<div class="abs feature" style="left:842px;top:1684px;width:226px;height:258px">
  <svg width="70" height="70" viewBox="0 0 70 70" fill="none" stroke="#fff" stroke-width="2.5"><rect x="8" y="12" width="54" height="48" rx="4"/><path d="M8 24 H62 M20 6 V16 M50 6 V16"/><circle cx="20" cy="34" r="2.5"/><circle cx="30" cy="34" r="2.5"/><circle cx="40" cy="34" r="2.5"/><circle cx="50" cy="34" r="2.5"/><circle cx="20" cy="46" r="2.5"/><circle cx="44" cy="48" r="9"/><path d="M40 48 L43 51 L49 45"/></svg>
  <h3>Within your reach</h3>
  <p>Follow-up appointments may<br>be done by video chat for your<br>convenience.</p>
</div>

<!-- pricing -->
<section class="abs pricing"></section>
<h2 class="abs pricing-title">Pricing</h2>
<p class="abs pricing-lead">Our pricing is simple, transparent and affordable.<br><span style="display:block;margin-top:8px">Membership Plan $80/mo, plus a one-time $99 enrollment fee.</span></p>
<ul class="abs perks">
  <li><svg width="20" height="20" viewBox="0 0 20 20"><circle cx="10" cy="10" r="8.5" fill="none" stroke="#222" stroke-width="1.6"/><path d="M8 6 L12 10 L8 14" fill="none" stroke="#222" stroke-width="1.6"/></svg>Includes all appointments, no co-pay</li>
  <li><svg width="20" height="20" viewBox="0 0 20 20"><circle cx="10" cy="10" r="8.5" fill="none" stroke="#222" stroke-width="1.6"/><path d="M8 6 L12 10 L8 14" fill="none" stroke="#222" stroke-width="1.6"/></svg>Relaxed, unrushed visits</li>
  <li><svg width="20" height="20" viewBox="0 0 20 20"><circle cx="10" cy="10" r="8.5" fill="none" stroke="#222" stroke-width="1.6"/><path d="M8 6 L12 10 L8 14" fill="none" stroke="#222" stroke-width="1.6"/></svg>Direct communication with your doctor via phone, email, video chat 24/7</li>
  <li><svg width="20" height="20" viewBox="0 0 20 20"><circle cx="10" cy="10" r="8.5" fill="none" stroke="#222" stroke-width="1.6"/><path d="M8 6 L12 10 L8 14" fill="none" stroke="#222" stroke-width="1.6"/></svg>Convenient online scheduling (no need to call during business hours)</li>
  <li><svg width="20" height="20" viewBox="0 0 20 20"><circle cx="10" cy="10" r="8.5" fill="none" stroke="#222" stroke-width="1.6"/><path d="M8 6 L12 10 L8 14" fill="none" stroke="#222" stroke-width="1.6"/></svg>Wholesale price for labs and medications</li>
</ul>
<div class="abs btn pricing-btn">Learn More</div>
<div class="abs photo-shadow"></div>
<div class="abs pricing-photo" role="img" aria-label="Group of friends embracing at sunset, seen from behind"></div>

<!-- footer -->
<svg class="abs footer" width="1200" height="400" viewBox="0 0 1200 400">
  <path d="M0 16 H480 C540 16 552 0 600 0 C648 0 660 16 720 16 H1200 V400 H0 Z" fill="#232323"/>
  <circle cx="600" cy="26" r="9" fill="none" stroke="#fff" stroke-width="1.6"/>
  <path d="M596 24 L600 28 L604 24" fill="none" stroke="#fff" stroke-width="1.6"/>
</svg>
<div class="abs foot-brand">
  <div class="brand-mark"></div>
  <div class="brand-name">LARKSPUR</div>
  <div class="brand-sub">INFECTIOUS DISEASE SPECIALISTS</div>
</div>
<div class="abs socials"><span></span><span></span><span></span><span></span></div>

<h3 class="abs foot-h" style="left:512px;top:2682px">Quick Links</h3>
<ul class="abs foot-links" style="left:518px;top:2730px">
  <li>Home</li><li>Specialties</li><li>Pricing</li><li>About Us</li><li>Faq</li>
</ul>
<ul class="abs foot-links" style="left:654px;top:2730px">
  <li>Blog</li><li>Join Us</li><li>Contact Us</li>
</ul>

<h3 class="abs foot-h" style="left:848px;top:2682px">Contact Us</h3>
<div class="abs contact" style="left:850px;top:2732px">
  <div class="row"><svg width="18" height="22" viewBox="0 0 18 22"><path d="M9 1 C4.5 1 1.5 4.5 1.5 8.5 C1.5 14 9 21 9 21 C9 21 16.5 14 16.5 8.5 C16.5 4.5 13.5 1 9 1 Z" fill="#fff"/><circle cx="9" cy="8.5" r="3" fill="#232323"/></svg><span>27 Fenwick Lane 12/4<br>Riverton, US</span></div>
  <div class="row"><svg width="20" height="20" viewBox="0 0 24 24"><path d="M6.6 10.8a15.1 15.1 0 0 0 6.6 6.6l2.2-2.2a1 1 0 0 1 1-.25 11.4 11.4 0 0 0 3.6.57 1 1 0 0 1 1 1V20a1 1 0 0 1-1 1A17 17 0 0 1 3 4a1 1 0 0 1 1-1h3.5a1 1 0 0 1 1 1c0 1.25.2 2.45.57 3.57a1 1 0 0 1-.25 1Z" fill="none" stroke="#fff" stroke-width="1.6"/></svg><span>1 (800) 555-0142</span></div>
  <div class="row"><svg width="22" height="18" viewBox="0 0 22 18"><rect x="1" y="2" width="20" height="14" fill="none" stroke="#fff" stroke-width="1.5"/><path d="M1 2 L11 10 L21 2" fill="none" stroke="#fff" stroke-width="1.5"/></svg><span>info@larkspurid.com</span></div>
</div>

<div class="abs foot-rule"></div>
<p class="abs legal" style="left:112px">© Copyrights 2019 | All Rights Reserved</p>
<p class="abs legal" style="left:746px">Terms &amp; Conditions</p>
<p class="abs legal" style="left:900px">Privacy Policy</p>
<p class="abs legal" style="left:1012px">Contact Us</p>

</body>
</html>
```